Velk Consulting -New consulting business in architecture, urban planning, and real estate development

We need a stationery design, including logo, business cards, etc, work for a new consulting business that works in the world of architectural, urban planning and real estate development.

The name of the company is "Velk Consulting". Velk is my last name but it of course also has the meaning 'cool' and 'hip'.

Target Market(s)

The business will provide boutique consulting services to high end clients that may include property developers, cities, etc.

Industry/Entity Type

Consultant

Contact Information for Business Card

VELK Consulting
First Name Last Name
Title
Phone number
Address
Website
Optional: Twitter handle

Logo Text

VELK Consulting

Font styles to use
Sans Serif

Colors

Designer to choose colors to be used in the design.

Requirements
Must have
• Simple design
• Easy to read font
• Modern
• Elegance
• Nice font that can be used for future reports, letters, etc.
• Good colour scheme that allows for the elegance to come through
Should not have
• Complex design ideas
• Complex logos
• Not a corporate feel and look

```html
<!DOCTYPE html>
<html lang="en">
<head>
<meta charset="utf-8">
<title>Velk Consulting — Letterhead</title>
<link href="https://fonts.googleapis.com/css2?family=Work+Sans:wght@400;500;600&family=Montserrat:wght@400;600&display=swap" rel="stylesheet">
<style>
  :root {
    --backdrop: #e6e6e6;
    --paper: #f1f1f1;
    --gold: #9c7a1c;
    --ink-dark: #2b2b2b;
    --ink-body: #6a6a6a;
    --ink-meta: #4a4a4a;
    --rule: #9a9a9a;
  }
  * { margin: 0; padding: 0; box-sizing: border-box; }
  html, body {
    width: 1200px;
    height: 1185px;
    overflow: hidden;
    background: var(--backdrop);
  }
  .letterhead {
    position: absolute;
    left: 209px;
    top: 42px;
    width: 782px;
    height: 1100px;
    background: var(--paper);
    font-family: "Work Sans", sans-serif;
  }
  .brand-name {
    position: absolute;
    top: 60px;
    left: 0;
    width: 100%;
    text-align: center;
    font-family: "Work Sans", sans-serif;
    font-weight: 500;
    font-size: 30px;
    letter-spacing: 2px;
    color: var(--gold);
  }
  .recipient {
    position: absolute;
    left: 73px;
    top: 265px;
    font-size: 14px;
    line-height: 17.5px;
    letter-spacing: 0.4px;
    color: var(--ink-meta);
  }
  .recipient .name,
  .recipient .role {
    font-weight: 600;
    color: var(--ink-dark);
  }
  .letter-date {
    position: absolute;
    right: 73px;
    top: 320px;
    font-size: 14px;
    letter-spacing: 0.6px;
    color: var(--ink-meta);
  }
  .letter-body {
    position: absolute;
    left: 57px;
    top: 435px;
    width: 666px;
    font-size: 11.3px;
    line-height: 23.5px;
    letter-spacing: 0.25px;
    color: var(--ink-body);
    text-align: justify;
  }
  .letter-body p { text-indent: 13px; }
  .letter-body p + p { margin-top: 23.5px; }
  .letter-footer {
    position: absolute;
    left: 0;
    top: 1022px;
    width: 100%;
    font-family: "Montserrat", sans-serif;
    font-size: 10.5px;
    color: var(--ink-dark);
    text-align: center;
  }
  .footer-address strong { font-weight: 600; }
  .footer-contacts {
    margin-top: 10px;
    display: flex;
    justify-content: center;
    align-items: center;
  }
  .contact-item {
    display: flex;
    align-items: center;
    gap: 6px;
    padding: 0 10px;
  }
  .contact-item + .contact-item { border-left: 1px solid var(--rule); }
  .contact-item svg { width: 13px; height: 13px; display: block; }
</style>
</head>
<body>
  <main class="letterhead">
    <div class="brand-name">VELK Consulting</div>

    <address class="recipient" style="font-style: normal;">
      <div class="name">MR. Daniel HARLOW</div>
      <div class="role">Managing Director</div>
      <div>12/08 Stone Tower</div>
      <div>Oregon - 987654321</div>
    </address>

    <div class="letter-date">Date : 01 July 2018</div>

    <section class="letter-body">
      <p>Lorem ipsum dolor sit amet, justo platonem in per, dicant constituto ne eam. Aeque persecuti sit ea, at vis commodo tractatos vituperata, sea an albucius forensibus. Wisi quodsi id qui, duo tempor aliquam assentior eu, no diceret tibique definiebas mei. Id nec noster facilisi mandamus.</p>
      <p>Nullam definiebas signiferumque pro te, vel mutat lobortis conceptam in. Usu justo minimum an, ne regione sanctus praesent usu, eam ut adipisci volutpat. Vel odio tibique consequat ne, in dicit gubergren appellantur vis, quo ei omnis elitr. Qui ne enim dictas dissentiet, pro nulla quodsi deseruisse te. Vide prima eloquentiam pro ei, agam dicta in pro, eu persius propriae constituam sea. Ius ut iriure oblique laboramus, cu sed fugit commune invenire, viris repudiandae ex vis.Nullam definiebas signiferumque pro te, vel mutat lobortis conceptam in. Usu justo minimum an, ne regione sanctus praesent usu, eam ut adipisci volutpat. Vel odio tibique consequat ne, in dicit gubergren appellantur vis, quo ei omnis elitr. Qui ne enim dictas dissentiet, pro nulla quodsi deseruisse te. Vide prima eloquentiam pro ei, agam dicta in pro, eu persius propriae constituam sea. Ius ut iriure oblique laboramus, cu sed fugit commune invenire, viris repudiandae ex vis.Nullam definiebas signiferumque pro te, vel mutat lobortis conceptam in. Usu justo minimum an, ne regione sanctus praesent usu, eam ut adipisci volutpat. Vel odio tibique consequat ne, in dicit gubergren appellantur vis, quo ei omnis elitr. Qui ne enim dictas dissentiet, pro nulla quodsi deseruisse te. Vide prima eloquentiam pro ei, agam dicta in pro, eu persius propriae constituam sea. Ius ut iriure oblique laboramus, cu sed fugit commune invenire, viris repudiandae ex vis.</p>
    </section>

    <footer class="letter-footer">
      <div class="footer-address"><strong>Velk Consulting</strong> - 118 N Linden Avenue, Ashford, MS 39120</div>
      <div class="footer-contacts">
        <span class="contact-item">
          <svg viewBox="0 0 16 16" aria-hidden="true"><path fill="#9c7a1c" d="M3.6 1.2l2.3 2.6-1.2 1.8c.9 2 2.6 3.7 4.6 4.6l1.8-1.2 2.6 2.3-1.4 2.6C6.6 13.7 2.3 9.4 1.1 3.6z"/></svg>
          000 000 0000
        </span>
        <span class="contact-item">
          <svg viewBox="0 0 16 16" aria-hidden="true"><rect x="1.5" y="3.5" width="13" height="9" fill="none" stroke="#9c7a1c" stroke-width="1.2"/><path d="M1.5 3.5L8 9l6.5-5.5" fill="none" stroke="#9c7a1c" stroke-width="1.2"/></svg>
          info@velkconsulting.com
        </span>
        <span class="contact-item">
          <svg viewBox="0 0 16 16" aria-hidden="true"><g fill="none" stroke="#9c7a1c" stroke-width="1.1"><circle cx="8" cy="8" r="6.3"/><ellipse cx="8" cy="8" rx="2.8" ry="6.3"/><path d="M1.7 8h12.6M2.6 4.8h10.8M2.6 11.2h10.8"/></g></svg>
          www.velkconsulting.com
        </span>
      </div>
    </footer>
  </main>
</body>
</html>
```